Vesta PR Website

Vesta PR are a PR company with a requirement for a new website. In consultation with the client, we have defined a wireframe for a homepage to show content and functionality. A PDF of the wire frame is attached.
Current site http://www.vesta-pr.co.uk/
Updates
If you are using Stock Photography - please use iStock
Dear All
Unfortunately, my client didn't like any of the designs submitted.
I've uploaded 3 examples of the type of photography that will appear in the carousel as supplied by the client.
Target Market(s)
Business to Business/Professionals - high value clients
Number of Pages Required
1 page
Requirements
Must have
- Colour scheme is attached as a .ase file from Kuler and can be viewed on Kuler if you search for 'VESTA PR Palette'
Corporate Typeface is Futura Book - use of Cufon is OK
Current Logo to be reatainedCall 2 Action Buttons will be controlled via the CMS so a generic background may be useful for these.
Nice to have
- RSS feeds

```html
<!DOCTYPE html>
<html lang="en">
<head>
<meta charset="utf-8">
<title>Vesta PR – Home</title>
<link rel="stylesheet" href="https://fonts.googleapis.com/css2?family=Jost:wght@400;500&family=Open+Sans:wght@400;700&family=Arimo:wght@400&display=swap">
<style>
  :root {
    --teal-dark: #0b5a6e;
    --teal-deep: #065a6e;
    --teal-bright: #0a9cbc;
    --mint: #a8dcd8;
    --nav-text: #1a6a7a;
    --heading: #0e5c70;
    --body: #333333;
    --panel: #f6f6f6;
    --white: #ffffff;
    --futura: 'Jost', sans-serif;
    --sans: 'Open Sans', sans-serif;
    --nav-font: 'Arimo', sans-serif;
  }
  * { margin: 0; padding: 0; box-sizing: border-box; }
  html, body { width: 1167px; height: 1200px; overflow: hidden; background: var(--white); }
  body { position: relative; font-family: var(--sans); color: var(--body); }
  a { color: inherit; text-decoration: none; }

  .site-header { position: absolute; left: 0; top: 0; width: 1167px; height: 82px; background: var(--teal-dark); }
  .brand { position: absolute; left: 42px; top: 14px;
    font-family: var(--futura); font-size: 42px; font-weight: 400; color: var(--white); letter-spacing: 3px; }
  .social { position: absolute; right: 14px; top: 30px; display: flex; align-items: center; gap: 14px;
    font-family: var(--sans); font-weight: 700; color: var(--white); font-size: 13px; }
  .social .label { letter-spacing: 1px; }
  .social a { font-size: 17px; }
  .social .sep { width: 2px; height: 26px; background: var(--mint); }

  .main-nav { position: absolute; left: 0; top: 82px; width: 1167px; height: 44px; background: var(--mint);
    display: flex; justify-content: center; align-items: center; gap: 7px;
    font-family: var(--nav-font); font-size: 20px; color: var(--nav-text); }

  .hero { position: absolute; left: 0; top: 126px; width: 1167px; height: 331px; }
  .hero-visual { position: absolute; left: 0; top: 0; width: 1167px; height: 331px; }
  .hero-menu { position: absolute; left: 44px; top: 22px; list-style: none;
    font-family: var(--futura); font-size: 28px; color: var(--white); }
  .hero-menu li { height: 61px; line-height: 50px; }

  .welcome { position: absolute; left: 44px; top: 474px; width: 565px; }
  .welcome h1 { font-family: var(--futura); font-weight: 400; font-size: 42px; color: var(--heading); line-height: 54px; }
  .welcome p { font-size: 13.5px; line-height: 16.4px; margin-bottom: 16px; }
  .welcome p.tight { margin-bottom: 0; }

  .card { position: absolute; top: 743px; width: 347px; height: 250px; background: var(--panel);
    border: 2px solid var(--teal-dark); padding: 4px 16px 4px 10px; }
  .card h2 { font-family: var(--futura); font-weight: 400; font-size: 29px; color: var(--heading); line-height: 36px; margin-bottom: 20px; }
  .card p { font-size: 13.5px; line-height: 21px; letter-spacing: 0.3px; }
  .client-news { left: 42px; padding-right: 24px; }
  .blog-entry { left: 434px; padding-right: 8px; }
  .blog-photo { float: right; width: 117px; height: 122px; margin: -52px 0 4px 8px; border: 2px solid var(--teal-dark); }

  .divider { position: absolute; left: 864px; top: 496px; height: 630px; border-left: 1px dotted #999; }

  .cta { position: absolute; left: 895px; width: 218px; height: 121px; border: 2px solid #111;
    background: linear-gradient(var(--teal-bright), var(--teal-deep));
    display: flex; align-items: center; justify-content: center;
    font-family: var(--futura); font-size: 30px; color: var(--white); }

  .site-footer { position: absolute; left: 0; top: 1013px; width: 1167px; height: 142px; background: var(--mint); }
  .footer-links { position: absolute; top: 16px; list-style: none; font-size: 13px; font-weight: 700;
    color: var(--teal-dark); letter-spacing: 0.6px; line-height: 21px; }
  .footer-links.services { left: 43px; }
  .footer-links.social-links { left: 338px; }
  .signup { position: absolute; left: 895px; top: 18px; width: 222px; }
  .signup h3 { font-family: var(--sans); font-size: 19px; font-weight: 700; color: var(--teal-dark); margin-bottom: 4px; }
  .signup .email { width: 220px; height: 38px; border: 1px solid var(--teal-dark); background: var(--white);
    font-size: 14px; font-weight: 700; color: var(--teal-dark); padding: 9px 10px; }
  .signup .subscribe { margin-top: 10px; width: 120px; height: 29px; border-radius: 4px;
    background: linear-gradient(var(--teal-bright), var(--teal-deep));
    font-family: var(--futura); font-size: 20px; color: var(--white); text-align: center; line-height: 29px; }

  .legal-bar { position: absolute; left: 0; top: 1155px; width: 1167px; height: 45px; background: var(--teal-dark);
    color: var(--white); font-size: 13px; font-weight: 700; text-align: right; padding: 13px 43px 0 0; letter-spacing: 0.6px; }
</style>
</head>
<body>
  <header class="site-header">
    <div class="brand">Vesta PR</div>
    <div class="social">
      <span class="label">Email Us:</span>
      <a href="#">Callwave</a><span class="sep"></span>
      <a href="#">Chirpline</a><span class="sep"></span>
      <a href="#">Friendnest</a>
    </div>
  </header>

  <nav class="main-nav">
    <a href="#">Home</a><span>|</span>
    <a href="#">Vesta Services</a><span>|</span>
    <a href="#">Press Office</a><span>|</span>
    <a href="#">Vesta Case Studies</a><span>|</span>
    <a href="#">Vesta People</a><span>|</span>
    <a href="#">Blog</a><span>|</span>
    <a href="#">Vesta News</a><span>|</span>
    <a href="#">Contact Us</a>
  </nav>

  <section class="hero">
    <svg class="hero-visual" viewBox="0 0 1167 331" width="1167" height="331">
      <defs>
        <linearGradient id="heroPhotoTone" x1="0" y1="0" x2="1" y2="1">
          <stop offset="0" stop-color="#7fc4c2"/>
          <stop offset="0.45" stop-color="#e8dcd0"/>
          <stop offset="1" stop-color="#f4f4f2"/>
        </linearGradient>
      </defs>
      <rect x="0" y="0" width="1167" height="331" fill="url(#heroPhotoTone)" role="img" aria-label="Carousel photograph of a smiling team of PR professionals"/>
      <path d="M0 0 H415 Q330 165 403 331 H0 Z" fill="#0b5a6e"/>
      <path d="M415 0 Q330 165 403 331" fill="none" stroke="#ffffff" stroke-width="3"/>
    </svg>
    <ul class="hero-menu">
      <li>Online Public Relations</li>
      <li>Media Relations</li>
      <li>Consumer Campaigns</li>
      <li>Crisis Public Relations</li>
      <li>Internal Communications</li>
    </ul>
  </section>

  <main>
    <section class="welcome">
      <h1>Welcome to Vesta PR</h1>
      <p>Vesta Public Relations is one of Scotland’s leading independent agencies. Founded in 2000, we were determined to create a public relations service with a real difference – hence the name.</p>
      <p class="tight">Vesta Public Relation's trademark is a fresh, creative and hard working approach to public relations. It is an approach that secures real results for our clients.</p>
      <p>We are an agency with intelligence, integrity and imagination offering a comprehensive, results driven public relations service covering traditional and online public relations strategy and support.</p>
    </section>

    <article class="card client-news">
      <h2>Client News</h2>
      <p>Lorem Ipsum is simply dummy text of the printing and typesetting industry. Lorem Ipsum has been the industry's standard dummy text ever since the 1500s, when an unknown printer took a galley of type. scrambled it to make a type specimen book.</p>
    </article>

    <article class="card blog-entry">
      <h2>Blog Entry</h2>
      <svg class="blog-photo" viewBox="0 0 117 122" role="img" aria-label="Portrait photograph of the blog author">
        <rect width="117" height="122" fill="#b9a58f"/>
      </svg>
      <p>Lorem Ipsum is simply dummy text of the printing and typesetting industry. Lorem Ipsum has been the industry's standard dummy text ever since the 1500s, when an unknown printer took a galley of type. scrambled it to make a type specimen book.</p>
    </article>

    <div class="divider"></div>

    <a class="cta" href="#" style="top:494px">Call to Action</a>
    <a class="cta" href="#" style="top:620px">Call to Action</a>
    <a class="cta" href="#" style="top:747px">Call to Action</a>
    <a class="cta" href="#" style="top:873px">Call to Action</a>
  </main>

  <footer class="site-footer">
    <ul class="footer-links services">
      <li>Online Public Relations</li>
      <li>Media Relations</li>
      <li>Consumer Campaigns</li>
      <li>Crisis Public Relations</li>
      <li>Internal Communications</li>
    </ul>
    <ul class="footer-links social-links">
      <li>Subscribe to RSS Feed</li>
      <li>Our Friendnest page</li>
      <li>Link Three</li>
      <li>Link Four</li>
    </ul>
    <div class="signup">
      <h3>E-News Sign-up</h3>
      <div class="email">Email Address</div>
      <div class="subscribe">Subscribe</div>
    </div>
  </footer>

  <div class="legal-bar">© Copyright Notice | Site Credit | Legal</div>
</body>
</html>
```